Upmarket Dessert Lounge needs a Business Card Design

We are an upmarket dessert lounge needing a business card to match our image.

We want something that is simple yet beautiful, feminine, classy, sophisticated and elegant. We want it to stand out and don't mind if it is bold.

The design should include our logo and colours of red or maroon with gold highlights. We don't mind if black is used.

Marlow & Quince

Target Market(s)

For those who like to indulge or treat themselves and give in to their temptations on good quality desserts.

Industry/Entity Type

Business

Requirements
Must have
• Must include our logo and our name

Marlow & Quince

M & Q

```html
<!DOCTYPE html>
<html lang="en">
<head>
<meta charset="utf-8">
<title>Marlow &amp; Quince — Business Card</title>
<link rel="stylesheet" href="https://fonts.googleapis.com/css2?family=Cormorant+Garamond:ital,wght@0,400;0,500;1,400&display=swap">
<style>
  :root {
    --backdrop: #2b2b2b;
    --card-red: #7f1519;
    --emboss-red: #661016;
    --tagline-red: #5e0f14;
    --gold: #f1d59b;
    --gold-soft: rgba(241, 213, 155, 0.35);
    --emboss-soft: rgba(102, 16, 22, 0.55);
  }
  * { margin: 0; padding: 0; box-sizing: border-box; }
  html, body { width: 1200px; height: 900px; overflow: hidden; }
  body {
    background: var(--backdrop);
    font-family: "Cormorant Garamond", Georgia, serif;
    position: relative;
  }
  .card {
    position: absolute;
    top: 308px;
    width: 513px;
    height: 284px;
    border-radius: 24px;
    background: var(--card-red);
    overflow: hidden;
  }
  .card--front { left: 73px; }
  .card--back { left: 615px; }

  /* front */
  .front-ornament {
    position: absolute;
    left: 100px; top: 70px;
    width: 312px; height: 145px;
    border-radius: 50%;
    background: radial-gradient(ellipse at center, transparent 45%, var(--emboss-soft) 46%, transparent 75%);
  }
  .front-name {
    position: absolute;
    left: 0; right: 0; top: 118px;
    text-align: center;
    font-size: 44px;
    font-weight: 400;
    letter-spacing: 1px;
    color: var(--emboss-red);
    line-height: 1;
  }
  .front-tagline {
    position: absolute;
    left: 0; right: 0; top: 251px;
    text-align: center;
    font-size: 12px;
    font-weight: 500;
    letter-spacing: 6.5px;
    text-transform: uppercase;
    color: var(--tagline-red);
  }

  /* back */
  .flourish {
    position: absolute;
    left: 201px;
    width: 112px; height: 32px;
    border-radius: 50%;
    background: radial-gradient(ellipse at center, var(--gold-soft) 0%, transparent 70%);
  }
  .flourish--top { top: 26px; }
  .flourish--bottom { top: 229px; }
  .back-logo-frame {
    position: absolute;
    left: 43px; top: 96px;
    width: 192px; height: 90px;
    border-radius: 50%;
    background: radial-gradient(ellipse at center, transparent 50%, var(--gold-soft) 52%, transparent 78%);
  }
  .back-name {
    position: absolute;
    left: 43px; top: 129px;
    width: 192px;
    text-align: center;
    font-size: 21px;
    font-weight: 400;
    color: var(--gold);
    line-height: 1;
    white-space: nowrap;
  }
  .divider {
    position: absolute;
    left: 258px; top: 94px;
    width: 1px; height: 98px;
    background: var(--gold);
    opacity: 0.8;
  }
  .contact {
    position: absolute;
    left: 280px; top: 100px;
    list-style: none;
    font-style: italic;
    font-size: 14.5px;
    line-height: 17.5px;
    color: var(--gold);
  }
</style>
</head>
<body>
  <section class="card card--front" aria-label="Card front">
    <div class="front-ornament" role="img" aria-label="Embossed scrollwork frame around the name"></div>
    <h1 class="front-name">MARLOW &amp; QUINCE</h1>
    <p class="front-tagline">Upmarket Dessert Lounge</p>
  </section>

  <section class="card card--back" aria-label="Card back">
    <div class="flourish flourish--top" role="img" aria-label="Gold ornamental flourish"></div>
    <div class="back-logo-frame" role="img" aria-label="Gold scrollwork frame around the name"></div>
    <h2 class="back-name">MARLOW &amp; QUINCE</h2>
    <div class="divider"></div>
    <ul class="contact">
      <li>Harbourview, South Coast</li>
      <li>800 555 01 23</li>
      <li>info@marlow-quince.com</li>
      <li>www.marlow-quince.com</li>
      <li>www.facebook.com/Marlow.Quince</li>
    </ul>
    <div class="flourish flourish--bottom" role="img" aria-label="Gold ornamental flourish"></div>
  </section>
</body>
</html>
```